KRWB new business card design

We need a business card design for our established business which is Australia wide however based in Melbourne. We are a young team of Financial Planners who specialize in Insurance and Basic super advice for people like us.

We are people who help our clients get things done in a timely and cost effective manner whilst having a good time and a laugh along the way.

We would like this to have a consistent feel with our new e-brochure which i have attached from a color and font perspective.

Industry/Entity Type

Business

Requirements
Must have
• We do not need specific address details rather just the states we are in:

VIC/NSW/QLD/TAS
Nice to have
• Curved edge to mate the brochure

```html
<!DOCTYPE html>
<html lang="en">
<head>
<meta charset="UTF-8">
<title>KRWB Business Card</title>
<link href="https://fonts.googleapis.com/css2?family=Arimo:wght@400;700&display=swap" rel="stylesheet">
<style>
  :root {
    --page-bg: #e6e6e6;
    --card-white: #f7f7f7;
    --card-dark: #2f2f2f;
    --brand-green: #6cc04a;
    --ink: #2b2b2b;
    --ink-soft: #3d3d3d;
    --on-dark: #ffffff;
  }
  * { box-sizing: border-box; margin: 0; padding: 0; }
  html, body { width: 1200px; height: 800px; overflow: hidden; }
  body {
    background: var(--page-bg);
    font-family: "Arimo", Arial, sans-serif;
    display: flex;
    align-items: center;
    justify-content: center;
    gap: 40px;
  }
  .card {
    width: 560px;
    height: 320px;
    border-radius: 4px;
    position: relative;
    overflow: hidden;
    box-shadow: 0 8px 24px rgba(0,0,0,0.18);
  }

  /* Front */
  .card--front { background: var(--card-white); display: flex; }
  .front__brand {
    width: 210px;
    display: flex;
    flex-direction: column;
    align-items: center;
    justify-content: center;
    gap: 10px;
  }
  .brand-mark {
    width: 52px; height: 52px;
    background: var(--brand-green);
    border-radius: 8px;
  }
  .brand-name {
    font-weight: 700;
    font-size: 40px;
    letter-spacing: -1px;
    color: var(--ink);
    line-height: 1;
  }
  .front__band {
    width: 100px;
    background: var(--brand-green);
    border-right: 8px solid var(--ink);
  }
  .front__details {
    flex: 1;
    min-width: 0;
    padding: 54px 16px 0 28px;
  }
  .person-name {
    font-weight: 700;
    font-size: 24px;
    color: var(--brand-green);
    line-height: 1.15;
  }
  .person-role {
    font-size: 20px;
    color: var(--ink-soft);
    margin-top: 2px;
  }
  .contact-list { list-style: none; margin-top: 34px; }
  .contact-list li {
    display: flex;
    align-items: center;
    gap: 8px;
    font-size: 16px;
    color: var(--ink);
    line-height: 26px;
    white-space: nowrap;
  }
  .contact-icon { width: 17px; height: 17px; flex-shrink: 0; }
  .service-states {
    margin-top: 14px;
    font-size: 14px;
    font-weight: 700;
    letter-spacing: 1px;
    color: var(--brand-green);
  }

  /* Back */
  .card--back {
    background: var(--card-dark);
    display: flex;
    flex-direction: column;
    align-items: center;
    justify-content: center;
  }
  .card--back .brand-mark { width: 70px; height: 70px; border-radius: 10px; }
  .back__brand {
    display: flex;
    flex-direction: column;
    align-items: center;
    gap: 14px;
  }
  .card--back .brand-name { color: var(--on-dark); font-size: 56px; }
  .back__web {
    margin-top: 22px;
    font-size: 16px;
    color: var(--on-dark);
  }
</style>
</head>
<body>

  <article class="card card--front">
    <div class="front__brand">
      <span class="brand-mark"></span>
      <span class="brand-name">KRWB</span>
    </div>
    <div class="front__band"></div>
    <div class="front__details">
      <h1 class="person-name">Harlow</h1>
      <p class="person-role">Manager</p>
      <ul class="contact-list">
        <li>
          <svg class="contact-icon" viewBox="0 0 18 18" aria-hidden="true">
            <rect width="18" height="18" rx="3" fill="#6cc04a"/>
            <path d="M5 4h2.5l1 3-1.5 1a6 6 0 0 0 3 3l1-1.5 3 1V13a1.5 1.5 0 0 1-1.5 1.5A9 9 0 0 1 3.5 5.5 1.5 1.5 0 0 1 5 4z" fill="#fff"/>
          </svg>
          03 9014 2270
        </li>
        <li>
          <svg class="contact-icon" viewBox="0 0 18 18" aria-hidden="true">
            <rect width="18" height="18" rx="3" fill="#6cc04a"/>
            <rect x="3.5" y="5" width="11" height="8" rx="1" fill="#fff"/>
            <path d="M3.8 5.4 9 9.6l5.2-4.2" fill="none" stroke="#6cc04a" stroke-width="1.2"/>
          </svg>
          hello@krwbplan.com.au
        </li>
        <li>
          <svg class="contact-icon" viewBox="0 0 18 18" aria-hidden="true">
            <rect width="18" height="18" rx="3" fill="#6cc04a"/>
            <circle cx="9" cy="9" r="5" fill="none" stroke="#fff" stroke-width="1.4"/>
            <path d="M4 9h10M9 4c-2.5 3-2.5 7 0 10M9 4c2.5 3 2.5 7 0 10" fill="none" stroke="#fff" stroke-width="1"/>
          </svg>
          www.krwbplan.com.au
        </li>
      </ul>
      <p class="service-states">VIC / NSW / QLD / TAS</p>
    </div>
  </article>

  <article class="card card--back">
    <div class="back__brand">
      <span class="brand-mark"></span>
      <span class="brand-name">KRWB</span>
    </div>
    <p class="back__web">www.krwbplan.com.au</p>
  </article>

</body>
</html>
```